Velmora Freightway Solutions Business cards

Would like a very unique design catchy but professional for business cards. Please use log provided.Marlon WellsCeo and Founder TransCon Logistix Solutions1-888-913-3225mwells@tlsolutionsus.comwww.tlsolutionsus.com

```html
<!DOCTYPE html>
<html lang="en">
<head>
<meta charset="utf-8">
<title>Velmora Freightway Solutions – Business Cards</title>
<link href="https://fonts.googleapis.com/css2?family=Lato:wght@400;700&display=swap" rel="stylesheet">
<style>
  :root {
    --backdrop: #e7e5e2;
    --navy: #0c2a44;
    --blue: #1474bf;
    --white: #ffffff;
    --brand-blue: #1c5fa8;
  }
  * { margin: 0; padding: 0; box-sizing: border-box; }
  html, body {
    width: 1200px; height: 960px; overflow: hidden;
    background: var(--backdrop);
    font-family: "Lato", Arial, sans-serif;
  }
  .canvas { position: relative; width: 1200px; height: 960px; }

  .card {
    position: absolute;
    border-radius: 30px;
    overflow: hidden;
    box-shadow: 0 6px 18px rgba(0,0,0,0.25);
  }

  /* Front card */
  .card-front {
    left: 237px; top: 47px; width: 720px; height: 405px;
    background: var(--navy);
    color: var(--white);
  }
  .front-brand {
    position: absolute; left: 0; right: 0; top: 118px;
    text-align: center;
    font-weight: 700; font-size: 62px; line-height: 1.05;
    letter-spacing: 1px;
  }
  .front-url {
    position: absolute; left: 0; right: 0; top: 298px;
    text-align: center;
    font-size: 19px; letter-spacing: 3px;
  }
  .front-url strong { font-weight: 700; }

  /* Back card */
  .card-back {
    left: 244px; top: 507px; width: 706px; height: 407px;
    background: var(--white);
  }
  .back-brand {
    position: absolute; left: 22px; top: 150px; width: 340px;
    text-align: center;
    color: var(--brand-blue);
    font-weight: 700; font-size: 30px; line-height: 1.15;
  }
  .url-strip {
    position: absolute; left: 376px; top: 61px; width: 32px; height: 287px;
    background: var(--navy);
  }
  .url-strip span {
    position: absolute; left: 50%; top: 50%;
    transform: translate(-50%, -50%) rotate(-90deg);
    white-space: nowrap;
    color: var(--white); font-size: 17px; letter-spacing: 2.5px;
  }
  .contact-panel {
    position: absolute; left: 408px; top: 61px; width: 298px; height: 287px;
    background: var(--blue);
    color: var(--white);
    padding: 36px 0 0 26px;
  }
  .person-name { font-weight: 700; font-size: 23px; line-height: 1.1; }
  .person-title { font-size: 18px; margin-top: 7px; }
  .address { font-size: 17px; line-height: 27px; margin-top: 24px; }
  .contact-line {
    display: flex; align-items: center; gap: 10px;
    font-size: 16.5px; line-height: 30px;
  }
  .contact-list { margin-top: 22px; }
  .contact-line svg { width: 15px; height: 15px; flex: none; }
</style>
</head>
<body>
<main class="canvas">

  <section class="card card-front" aria-label="Business card front">
    <div class="front-brand">Velmora<br>Freightway Solutions</div>
    <div class="front-url">www.<strong>vfwayroutes</strong>.com</div>
  </section>

  <section class="card card-back" aria-label="Business card back">
    <div class="back-brand">Velmora Freightway Solutions</div>

    <div class="url-strip"><span>www.vfwayroutes.com</span></div>

    <div class="contact-panel">
      <div class="person-name">DORIAN PIKE</div>
      <div class="person-title">CEO AND FOUNDER</div>
      <div class="address">2460 Larkspur Ridge Rd<br>Atlanta, GA 30319</div>
      <div class="contact-list">
        <div class="contact-line">
          <svg viewBox="0 0 16 16" aria-hidden="true"><circle cx="8" cy="8" r="7" fill="none" stroke="#fff" stroke-width="1.4"/><path d="M5.5 4.5l1.6 1.8-1 1.1c.6 1.2 1.4 2 2.5 2.5l1.1-1 1.8 1.6-1 1.3c-2.8-.4-5.2-2.8-5.6-5.6z" fill="#fff"/></svg>
          <span>1-888-470-6158</span>
        </div>
        <div class="contact-line">
          <svg viewBox="0 0 16 16" aria-hidden="true"><path d="M1 6l7-4 7 4v8H1z" fill="#fff"/><path d="M1 6l7 5 7-5" fill="none" stroke="#1474bf" stroke-width="1.3"/></svg>
          <span>dpike@vfwayroutes.com</span>
        </div>
      </div>
    </div>
  </section>

</main>
</body>
</html>
```